Business Cards

Need business card design that I can update for new employees and details. Needs to incorporate our logo, be bright and fun (in line with tourism and holidays)
Would like a Map of Western Australia on the front with locations all the caravan parks we own (just purchased Tom Price so please include that as well as others listed on our website).
Target Market(s)
Famillies
Contact Information for Business Card
5 Cards -
Neil Perrow (Director) e: perrow@wattlebay.com.au p: 0491 570 156
Mira Perrow (Director) e: perrow@wattlebay.com.au p: 0491 570 157
Owen Halvey (General Manager) e: halvey@wattlebay.com.au p: 0491 570 158
Helen Halvey (General Manager) e: halvey@wattlebay.com.au p: 0491 570 159
Colin Danby (Training and Operations Manager) - e: danby@wattlebay.com.au p:0491 570 110
Colors
Look and feel

```html
<!DOCTYPE html>
<html lang="en">
<head>
<meta charset="utf-8">
<title>Wattle Bay Tourist Parks – Business Card</title>
<link rel="stylesheet" href="https://fonts.googleapis.com/css2?family=Tinos:wght@400;700&family=Roboto:wght@400&display=swap">
<style>
  :root {
    --backdrop: #2a2a2a;
    --paper: #f3f3f3;
    --teal: #3db8c1;
    --teal-mark: #5fb8ad;
    --ink: #555555;
    --ink-dark: #3f3f3f;
    --white: #ffffff;
  }
  * { margin: 0; padding: 0; box-sizing: border-box; }
  html, body {
    width: 1200px; height: 960px; overflow: hidden;
    background: var(--backdrop);
  }
  .canvas { position: relative; width: 1200px; height: 960px; }

  .card { position: absolute; width: 600px; height: 343px; overflow: hidden; }
  .card--front { left: 314px; top: 113px; background: var(--paper); }
  .card--back { left: 311px; top: 472px; background: var(--teal); }

  /* front */
  .name-band {
    position: absolute; left: 203px; top: 54px; width: 397px; height: 71px;
    background: var(--teal);
  }
  .brand-square {
    position: absolute; left: 127px; top: 54px; width: 72px; height: 71px;
    background: var(--teal-mark);
    outline: 2px solid var(--teal-mark); outline-offset: 1px;
  }
  .brand-name {
    position: absolute; left: 52px; top: 113px; width: 222px;
    font-family: "Tinos", serif; font-weight: 400; color: var(--ink);
    text-align: center; text-transform: uppercase; white-space: nowrap;
  }
  .brand-name .line-main { display: block; font-size: 22px; letter-spacing: 3px; line-height: 34px; }
  .brand-name .line-main::first-letter { font-size: 32px; }
  .brand-name .line-sub { display: block; font-size: 12px; letter-spacing: 3px; line-height: 14px; }

  .holder {
    position: absolute; left: 332px; top: 69px;
    font-family: "Tinos", serif; font-weight: 700; color: var(--white);
    text-transform: uppercase;
  }
  .holder-name { font-size: 21px; line-height: 24px; }
  .holder-role { font-size: 15px; line-height: 18px; }

  .contact-list {
    position: absolute; left: 332px; top: 229px; list-style: none;
    font-family: "Roboto", sans-serif; font-size: 14.5px; color: var(--ink-dark);
  }
  .contact-list li { display: flex; align-items: center; height: 19px; }
  .contact-list svg { width: 13px; height: 13px; margin-right: 9px; fill: var(--teal); }

  /* back */
  .back-square {
    position: absolute; left: 255px; top: 100px; width: 91px; height: 91px;
    border: 3px solid var(--white);
  }
  .back-brand {
    position: absolute; left: 0; top: 172px; width: 600px;
    font-family: "Tinos", serif; font-weight: 400; color: var(--white);
    text-align: center; text-transform: uppercase; white-space: nowrap;
  }
  .back-brand .line-main { display: block; font-size: 30px; letter-spacing: 4px; line-height: 50px; }
  .back-brand .line-main::first-letter { font-size: 44px; }
  .back-brand .line-sub { display: block; font-size: 16px; letter-spacing: 4px; line-height: 18px; }
  .back-url {
    position: absolute; left: 0; top: 293px; width: 600px; text-align: center;
    font-family: "Roboto", sans-serif; font-size: 14px; letter-spacing: 2.5px; color: var(--white);
  }
</style>
</head>
<body>
<main class="canvas">
  <section class="card card--front" aria-label="Card front">
    <div class="name-band"></div>
    <div class="brand-square"></div>
    <div class="brand-name">
      <span class="line-main">Wattle Bay</span>
      <span class="line-sub">Tourist Parks</span>
    </div>
    <div class="holder">
      <p class="holder-name">Neil Perrow</p>
      <p class="holder-role">Director</p>
    </div>
    <ul class="contact-list">
      <li>
        <svg viewBox="0 0 24 24" aria-hidden="true"><path d="M6.6 10.8c1.4 2.8 3.8 5.1 6.6 6.6l2.2-2.2c.3-.3.7-.4 1-.2 1.1.4 2.3.6 3.6.6.6 0 1 .4 1 1V20c0 .6-.4 1-1 1C10.6 21 3 13.4 3 4c0-.6.4-1 1-1h3.5c.6 0 1 .4 1 1 0 1.3.2 2.5.6 3.6.1.3 0 .7-.2 1z"/></svg>
        0491 570 156
      </li>
      <li>
        <svg viewBox="0 0 24 24" aria-hidden="true"><path d="M2 5h20v14H2z"/><path d="M3 6l9 6.3L21 6v1.6l-9 6.3-9-6.3z" fill="#f3f3f3"/></svg>
        perrow@wattlebay.com.au
      </li>
      <li>
        <svg viewBox="0 0 24 24" aria-hidden="true"><circle cx="12" cy="12" r="10"/><path d="M7 7c2 1 3 3 2 5s1 3 2 4M15 5c-1 2 1 3 3 3M14 14c1 1 3 1 4 3" stroke="#f3f3f3" stroke-width="1.6" fill="none"/></svg>
        www.wattlebay.com.au
      </li>
    </ul>
  </section>

  <section class="card card--back" aria-label="Card back">
    <div class="back-square"></div>
    <div class="back-brand" style="top: 196px;">
      <span class="line-main">Wattle Bay</span>
      <span class="line-sub">Tourist Parks</span>
    </div>
    <p class="back-url">www.wattlebay.com.au</p>
  </section>
</main>
</body>
</html>
```